MRW (Orsolya Vendel Care) Website supporting women to live a healthy lifestyle

Hi
I'm thrilled to be working together to bring a fresh look to my website! As an Integrative Health Practitioner, my mission is to support and empower women on their journey to reclaim their health and well-being. The website should feel inviting, with a soft and nurturing energy that also radiates vibrancy and vitality.

Design & Aesthetic:

I'd love to focus on rich rose gold tones
It should feel soft and approachable yet energetic and lively.

Functional Needs:

The site will support both my coaching services
and product sales, so it’s essential to have an intuitive and user-friendly shopping experience.
I'd love some exciting interactive features that keep visitors engaged and make the journey through the site feel seamless and uplifting.

Please let me know if there’s any additional information you need from me to bring this vision to life!

Thank you for your attention to these details! Here are some ideas I like to see Layout Ideas

Hero Section: An inviting header with a subtle half-moon background for a touch of healing energy.

Navigation & Logo: Place my logo in gold on the top left and use simple navigation links with a rose gold hover effect.

Section Dividers: Use small celestial icons, like a crescent moon, as dividers to create flow and add a bit of magic.

Product & Service Section: A soft rose gold gradient background to highlight products, with circular or wave accents around images.

Footer: Deep rose gold background with a half-moon icon to end with a warm invitation to connect.

Uploading an AI-generated image (it is a bit over the top but it captures the feel I like), with a hint of spirituality and femininity, along with elements like the half moon and colors. :) I'm also uploading my logos, and I have each option available in both color schemes.

Best,
Orsolya

• Playfair Display (Headings) & Lora (Body Text)

• Cartwell

```html
<!DOCTYPE html>
<html lang="en">
<head>
<meta charset="utf-8">
<title>Orsolya Vendel Care</title>
<link href="https://fonts.googleapis.com/css2?family=Playfair+Display:wght@600;700&family=Lora:wght@400;500;600&display=swap" rel="stylesheet">
<style>
:root{
  --rose-light:#f5dcd6;
  --rose:#ebb6a8;
  --rose-mid:#e5ab9c;
  --rose-deep:#dfa595;
  --brown:#9f5646;
  --brown-soft:#a8604f;
  --text:#7d4538;
  --card-line:#f1c9bf;
  --white:#fff;
}
*{margin:0;padding:0;box-sizing:border-box}
html,body{width:1200px;height:2701px;overflow:hidden}
body{
  position:relative;font-family:"Lora",serif;color:var(--text);
  background:linear-gradient(180deg,#f6dcd7 0,#efc3b8 300px,#e6ad9e 560px,#e8b0a2 1000px,#efc2b6 1120px,#e8b2a4 1300px,#e3a898 1700px,#e6ae9f 2300px);
}
.abs{position:absolute}
.serif{font-family:"Playfair Display",serif}
.btn{position:absolute;display:flex;align-items:center;justify-content:center;background:var(--brown-soft);color:#fbe7e1;border-radius:20px;font-family:"Playfair Display",serif;font-weight:600}
.lotus{position:absolute;width:68px;height:34px;border-radius:50% 50% 10px 10px;background:radial-gradient(ellipse at 50% 100%,#fbe3dc,#f0c3b6 60%,transparent 72%)}
.divider{position:absolute;height:2px;background:var(--brown-soft)}

/* header */
.logo{left:133px;top:31px;width:155px;text-align:center;color:#c98d7b}
.logo-mark{width:74px;height:74px;margin:0 auto;border:1.5px solid #c98d7b;border-radius:50%;display:flex;align-items:center;justify-content:center;font-size:22px;font-weight:500;letter-spacing:1px}
.logo-name{font-size:15px;letter-spacing:1px;margin-top:8px;white-space:nowrap}
.logo-care{font-size:12px;letter-spacing:4px}
.nav{top:38px;left:558px;display:flex;align-items:center;font-size:13.5px;color:var(--text)}
.nav a{color:inherit;text-decoration:none;padding:5px 14px;margin-right:2px}
.nav a.active{background:var(--brown-soft);color:#fff;border-radius:14px}
.nav .mail{display:flex;align-items:center;margin-left:14px;gap:10px}
.nav .mail i{width:20px;height:20px;border-radius:50%;background:var(--brown-soft);display:flex;align-items:center;justify-content:center}

.hero-title{left:131px;top:205px;font-size:51px;line-height:55px;font-weight:700;color:var(--brown)}
.hero-sub{left:131px;top:441px;font-size:21px;color:var(--text)}
.hero-moon{left:642px;top:133px;width:433px;height:431px;border-radius:50%;
  background:radial-gradient(circle at 72% 40%,transparent 44%,rgba(0,0,0,0) 45%),radial-gradient(circle at 35% 60%,#d39884,#eac0b0 55%,#f3d3c8 70%,transparent 71%)}

/* about */
.about-photo{left:142px;top:617px;width:401px;height:418px;border-radius:50%;background:radial-gradient(circle at 45% 40%,#b37a5c,#6e4433 60%,#4a2e24)}
.about-title{left:626px;top:640px;font-size:46px;line-height:58px;font-weight:700;color:var(--brown)}
.about-text{left:630px;top:812px;width:400px;font-size:15px;line-height:21.2px;color:var(--text)}

/* products */
.section-title{left:0;width:1200px;text-align:center;font-size:47px;font-weight:700;color:var(--brown)}
.card{position:absolute;top:1369px;width:223px;height:309px;border:1px solid var(--card-line);text-align:center}
.card.featured{background:linear-gradient(180deg,#eba69c,#f6d6cf 60%,#fbe9e4);border-color:transparent}
.card-img{position:absolute;left:50%;top:-76px;width:152px;height:152px;margin-left:-76px;border-radius:50%;border:3px solid #fbeae5;box-shadow:0 0 0 14px rgba(251,228,222,.35)}
.card h3{position:absolute;top:136px;left:0;width:100%;font-family:"Playfair Display",serif;font-weight:600;font-size:17px;line-height:21px;color:var(--brown-soft)}
.card p{position:absolute;top:197px;left:20px;right:20px;font-size:10.5px;line-height:14px;color:var(--text)}
.card .btn{left:66px;top:298px;width:90px;height:27px;font-size:12px}

/* testimonials */
.quote{position:absolute;top:1930px;width:300px;height:255px;background:linear-gradient(180deg,rgba(245,205,194,.55),rgba(247,208,198,.9));border:1px solid #f3cfc5}
.quote .mark{position:absolute;left:18px;top:6px;font-family:"Playfair Display",serif;font-size:70px;line-height:70px;color:#f4d5cc}
.quote p{position:absolute;left:41px;top:57px;width:222px;font-size:12.5px;line-height:17.6px;color:var(--text)}
.quote .line{position:absolute;left:41px;top:200px;width:31px;height:1.5px;background:var(--brown-soft)}
.quote .name{position:absolute;left:41px;top:214px;font-size:11.5px;font-weight:600;color:var(--text)}
.dots{left:558px;top:2232px;display:flex;gap:9px}
.dots span{width:9px;height:9px;border-radius:50%;background:#fff}
.dots span:first-child{background:linear-gradient(90deg,var(--brown-soft) 50%,#fff 50%)}

/* footer */
.footer{left:0;top:2311px;width:1200px;height:390px;background:#e7ada0}
.footer-logo{left:0;width:1200px;top:2355px;text-align:center;color:var(--brown-soft)}
.footer-logo .logo-mark{width:104px;height:104px;border-color:var(--brown-soft);font-size:30px}
.footer-logo .logo-name{font-size:24px;margin-top:14px}
.footer-logo .logo-care{font-size:16px;letter-spacing:6px}
.footer-nav{left:0;width:1200px;top:2542px;display:flex;justify-content:center;gap:36px;font-size:13.5px;color:var(--text)}
.follow{left:0;width:1200px;top:2591px;display:flex;justify-content:center;align-items:center;gap:6px;font-size:11px;color:var(--text)}
.follow b{font-weight:400;margin-right:10px}
.follow span{width:22px;height:22px;border-radius:50%;background:var(--brown)}
.copy{left:0;width:1200px;top:2642px;text-align:center;font-size:9px;color:#d1958a}
</style>
</head>
<body>

<div class="abs logo">
  <div class="logo-mark">MRW</div>
  <div class="logo-name">ORSOLYA VENDEL</div>
  <div class="logo-care">CARE</div>
</div>

<nav class="abs nav">
  <a class="active" href="#">HOME</a>
  <a href="#">ABOUT US</a>
  <a href="#">SERVICES</a>
  <a href="#">CONTACT US</a>
  <span class="mail"><i><svg width="11" height="8" viewBox="0 0 11 8"><rect x=".5" y=".5" width="10" height="7" fill="none" stroke="#fff"/><path d="M.5.5l5 4 5-4" fill="none" stroke="#fff"/></svg></i>info@mrwcare.au</span>
</nav>

<div class="lotus" style="left:525px;top:130px" role="img" aria-label="Small lotus ornament"></div>
<h1 class="abs serif hero-title">Achieve Peak Health,<br>Productivity and<br>Energy with<br>zero Stress</h1>
<p class="abs hero-sub">Integrative health coaching brings together</p>
<a class="btn" style="left:130px;top:494px;width:126px;height:39px;font-size:17px">Read More</a>
<div class="abs hero-moon" role="img" aria-label="Ornate rose gold crescent moon with floral engravings"></div>

<div class="abs about-photo" role="img" aria-label="Photo of a smiling woman framed in a crescent shape"></div>
<h2 class="abs serif about-title">About<br>Orsolya Vendel</h2>
<div class="lotus" style="left:763px;top:650px" role="img" aria-label="Small lotus ornament"></div>
<div class="divider" style="left:630px;top:777px;width:46px"></div>
<p class="abs about-text">I am a bold and inspiring multidimensional healer, driven by a mission to empower individuals to take control of their health and live a life of limitless potential. My purpose is to guide men and women on a journey of self-discovery and transformation, helping them cultivate a deep sense of self-love and self-awareness.</p>
<a class="btn" style="left:629px;top:970px;width:100px;height:30px;font-size:13px">Read More</a>

<div class="lotus" style="left:566px;top:1080px" role="img" aria-label="Small lotus ornament"></div>
<h2 class="abs serif section-title" style="top:1127px">Our Products</h2>
<div class="divider" style="left:577px;top:1214px;width:46px"></div>

<div class="card" style="left:126px">
  <div class="card-img" style="background:radial-gradient(circle,#c9a06a,#6f8a45 60%,#f4ece6)" role="img" aria-label="Plate of assorted healthy foods"></div>
  <h3>Personalized<br>Nutrition Plans</h3>
  <p>Lorem ipsum dolor sit amet, con sectetur adipiscing elit, sed do eiusmod tempor incididunt ut labore et dolor magna aliqua. Ut enim ad minim veniam, quis nostrud exercitation ullamco</p>
  <a class="btn">Read More</a>
</div>
<div class="card featured" style="left:366px">
  <div class="card-img" style="background:radial-gradient(circle,#d8b09a,#7ea6ab 60%,#e9eef0)" role="img" aria-label="Woman holding a supplement bottle"></div>
  <h3>Supplements for<br>Women's Health</h3>
  <p>Lorem ipsum dolor sit amet, con sectetur adipiscing elit, sed do eiusmod tempor incididunt ut labore et dolor magna aliqua. Ut enim ad minim veniam, quis nostrud exercitation ullamco</p>
  <a class="btn">Read More</a>
</div>
<div class="card" style="left:609px">
  <div class="card-img" style="background:radial-gradient(circle,#b88c6e,#3f5a6e 60%,#223445)" role="img" aria-label="Woman leading a workshop"></div>
  <h3>Workshops and<br>Cooking Classes</h3>
  <p>Lorem ipsum dolor sit amet, con sectetur adipiscing elit, sed do eiusmod tempor incididunt ut labore et dolor magna aliqua. Ut enim ad minim veniam, quis nostrud exercitation ullamco</p>
  <a class="btn">Read More</a>
</div>
<div class="card" style="left:853px">
  <div class="card-img" style="background:radial-gradient(circle,#c99a80,#3c5f7d 55%,#5d7a45)" role="img" aria-label="Woman eating a fresh salad"></div>
  <h3>Nutrition<br>Coaching</h3>
  <p>Lorem ipsum dolor sit amet, con sectetur adipiscing elit, sed do eiusmod tempor incididunt ut labore et dolor magna aliqua. Ut enim ad minim veniam, quis nostrud exercitation ullamco</p>
  <a class="btn">Read More</a>
</div>

<div class="lotus" style="left:566px;top:1760px" role="img" aria-label="Small lotus ornament"></div>
<h2 class="abs serif section-title" style="top:1804px">Testimonials</h2>
<div class="divider" style="left:577px;top:1884px;width:46px"></div>

<div class="quote" style="left:131px">
  <div class="mark">&ldquo;</div>
  <p>Orsolya is a passionate health mentor who genuinely cares about her clients and is generous with her time and knowledge. Her authentic, skilled, compassionate nature makes her an absolute joy to work with.</p>
  <div class="line"></div><div class="name">Delphine</div>
</div>
<div class="quote" style="left:451px">
  <div class="mark">&ldquo;</div>
  <p>I am now so knowledgeable about food and health. And I know if I fall off track, it's ok because I know how to find my way back from experience I have had both with the detox program has done that twice and the three month CBO protocol to rebalance my gut.</p>
  <div class="line"></div><div class="name">Marisol</div>
</div>
<div class="quote" style="left:772px">
  <div class="mark">&ldquo;</div>
  <p>Orsolya is practical but also realistic. Setting small achievable easy understanding lifestyle changes was important to get started with making change. Orsolya provided a list of healthy changes resulting from feedback from our discussion.</p>
  <div class="line"></div><div class="name">Everett</div>
</div>

<div class="abs dots"><span></span><span></span><span></span><span></span><span></span></div>

<div class="abs footer"></div>
<div class="abs footer-logo">
  <div class="logo-mark">MRW</div>
  <div class="logo-name">ORSOLYA VENDEL</div>
  <div class="logo-care">CARE</div>
</div>
<div class="abs footer-nav"><span>HOME</span><span>ABOUT US</span><span>SERVICES</span><span>CONTACT US</span></div>
<div class="abs follow"><b>FOLLOW US</b><span></span><span></span><span></span><span></span></div>
<div class="abs copy">Copyright © 2024 All Rights Reserved</div>

</body>
</html>
```